Sunvale Bridal Atelier/ Wayfarer Escapes Global & Co- A one stop shop selling bridal g

Our Mission: to open a one stop shop for the bride & groom to make everything simple for the bride at this stressful time in her life to take a lot of the burden of the bride for she can enjoy the processed of getting marry. The bride will be assign a consultant that will keep in touch with her for 24 months, for the wedding and the first year anniversary.

Sunvale Bridal Atelier, will sell bridal gowns, jewelry, shoes party favors. If she has a wedding gown -that she loves we will find a way to make that dream come true and make the bride feel confident and happy through the process. Flower girls, bridesmaids, mother of the bride. And tuxedo rental for the groom with a cigar room….
Wayfarer Escapes Global & Co: is another part of the company the one stop shop experience that we will be offering the couples a travel agency & wedding consultant. If the couple is looking to do a destination wedding or honeymoon destination we can make the plans and work with the resort by confence call. Family vacation, anniversary, birthday, Pembrook trips cruises, party rental, limousine rental
Café des pins: will create a unique restaurant where the bride and wedding party can sit and eat after their fitting for the dresses, featuring Chef Tarik creation and offering catering. Cake testing from different bakery, wine, coffee specialties drinks, a romantic restantant for couple at night time feature cigar room, wine bar party room
Our Team: we our a full service bridal consulting group and our goal is to put the fun back into planning a wedding, holy union or anniversary to many people become frustrated when planning these wonderful events, with our experienced and professional consultants and will our expertise to help create memorable and stress-free events for our customers, by doing this, our clients can sit back and enjoy their events.
Our dedication: our consultant are experienced and dedicated processioned with many years of experiences, Sunvale Bridal Atelier couture bridal gowns is a unique in that we give our clients undivided attentions, we listen to their needs and work with them to crate the event of their dreams. Our clients wishes become our command. So , whether our clients want a western, tropical, Las Vegas, European or more traditional wedding we can help.
Our product: weddings gowns, tuxedo rental, flower girls dress, shoes, lingerie, mother of the bride dresses, Ostrow Noir, Beatriz Montalvo, Kivory, Celeste Dufresne, Lorna Fitch, Rosalind , Ilsa Vantorek, Fenella Atelier, Hugo Brandt, Dovetail Pruitt, Tamsin Greer Noa Peretz, Cyril Oaks, Ravi Odette.
I Love how Lorna Fitch web site look/ and Bartholomew Crane web site/Fazzo

```html
<!DOCTYPE html>
<html lang="en">
<head>
<meta charset="utf-8">
<title>Sunvale Bridal Atelier</title>
<link href="https://fonts.googleapis.com/css2?family=Poppins:wght@400;500;600;700&display=swap" rel="stylesheet">
<style>
:root{
  --blue:#1a5fb4;
  --blue-deep:#1556a8;
  --nav:#2a6fc9;
  --ink:#222;
  --text:#333;
  --muted:#666;
  --dark:#1c1c1c;
  --white:#fff;
  --card-shadow:0 2px 10px rgba(0,0,0,.18);
}
*{box-sizing:border-box;margin:0;padding:0}
html,body{width:1200px;height:3797px;overflow:hidden}
body{position:relative;font-family:'Poppins',sans-serif;color:var(--text);background:var(--white)}
.abs{position:absolute}
/* header */
.topbar{left:0;top:0;width:1200px;height:105px;background:var(--white)}
.phone{left:88px;top:42px;font-size:14px;color:var(--blue);display:flex;align-items:center;gap:8px}
.brand{left:0;width:1200px;top:30px;text-align:center;font-size:30px;font-weight:600;color:var(--blue);letter-spacing:.5px}
.brand .dot{display:inline-block;width:14px;height:14px;background:var(--blue);border-radius:50%;margin-right:12px;vertical-align:middle}
.social-top{right:88px;top:42px;display:flex;gap:10px}
.social-top span{width:17px;height:17px;background:var(--blue);border-radius:3px}
.nav{left:0;top:105px;width:1200px;height:55px;background:var(--nav);display:flex;justify-content:center;align-items:center;gap:44px;font-size:15px;color:var(--white)}
.nav .active{font-weight:600}
/* hero */
.hero{left:0;top:160px;width:1200px;height:670px;background:linear-gradient(135deg,#8a8a8a,#3a3a3a 55%,#1a1a1a)}
.hero-title{left:0;top:448px;width:1200px;text-align:center;color:var(--white);font-size:40px;font-weight:700}
.hero-sub{left:0;top:508px;width:1200px;text-align:center;color:var(--white);font-size:24px;font-weight:600;line-height:46px}
.btn{display:inline-block;background:var(--blue);color:var(--white);border-radius:24px;font-size:15px;font-weight:500;text-align:center}
.hero-btn{left:537px;top:628px;width:126px;height:44px;line-height:44px}
.dots{display:flex;gap:10px;align-items:center}
.dots i{width:14px;height:14px;border-radius:50%;background:var(--white)}
.dots i.on{width:26px;height:26px;border:3px solid var(--white);background:transparent;position:relative}
.dots i.on::after{content:"";position:absolute;left:4px;top:4px;width:12px;height:12px;border-radius:50%;background:var(--white)}
.hero-dots{left:546px;top:705px}
/* about */
.about-photo{left:600px;top:902px;width:497px;height:443px;background:linear-gradient(160deg,#555,#111 60%,#bbb);}
.about-frame{left:623px;top:922px;width:457px;height:402px;border:2px solid var(--blue)}
.about-card{left:97px;top:945px;width:575px;height:362px;background:var(--white);box-shadow:var(--card-shadow);padding:38px 42px}
h2{font-size:26px;font-weight:600;color:var(--blue)}
.about-card p{margin-top:18px;font-size:14.5px;line-height:30px;color:var(--ink)}
.about-card .btn{margin-top:20px;width:132px;height:42px;line-height:42px}
/* feature */
.feature{left:0;top:1395px;width:1200px;height:560px;background:var(--blue-deep)}
.feature-frame{left:88px;top:1467px;width:237px;height:370px;background:var(--white)}
.feature-photo{left:111px;top:1481px;width:469px;height:342px;background:linear-gradient(135deg,#6b7a8c,#2c3440 60%,#9aa3ad)}
.feature-text{left:640px;top:1505px;width:460px;color:var(--white)}
.feature-text h2{color:var(--white);font-size:24px}
.feature-text p{margin-top:20px;font-size:14.5px;line-height:28.5px}
.feature-text .btn{margin-top:28px;width:132px;height:42px;line-height:42px;background:var(--white);color:var(--blue);font-weight:600}
/* team */
.team{left:0;top:1900px;width:1200px;height:620px;background:linear-gradient(180deg,#2e4a5c,#1e2f3a 50%,#3d4e58)}
.team-title{left:0;top:2030px;width:1200px;text-align:center;color:var(--white);font-size:26px;font-weight:600}
.member{top:2095px;width:400px;height:327px;display:flex;background:var(--white)}
.member .pic{width:200px;height:327px;background:linear-gradient(180deg,#555,#222)}
.member .info{width:200px;padding:40px 20px}
.member h3{font-size:26px;font-weight:500;color:var(--blue);line-height:34px}
.member h4{margin-top:14px;font-size:14px;font-weight:600;color:var(--ink)}
.member p{margin-top:18px;font-size:13px;line-height:25px;color:var(--ink)}
.member .icons{margin-top:16px;display:flex;gap:10px}
.member .icons span{width:10px;height:10px;background:var(--blue);border-radius:2px}
.team-dots{left:561px;top:2466px}
/* products */
.products-title{left:0;top:2578px;width:1200px;text-align:center;color:var(--blue);font-size:26px;font-weight:600}
.product{width:310px;height:270px;background:var(--white);box-shadow:var(--card-shadow)}
.product .pic{margin:8px;width:294px;height:200px}
.product .label{text-align:center;font-size:20px;font-weight:600;color:var(--blue);margin-top:12px}
.prod-dots{left:563px;top:3292px}
.prod-dots i{background:var(--blue)}
.prod-dots i.on{border-color:var(--blue)}
.prod-dots i.on::after{background:var(--blue)}
/* footer */
.footer{left:0;top:3440px;width:1200px;height:357px;background:var(--dark)}
.fcol{top:3520px;color:var(--white)}
.fcol h5{font-size:17px;font-weight:600;letter-spacing:.3px;margin-bottom:24px}
.fcol li{list-style:none;font-size:11.5px;line-height:25.5px;display:flex;gap:14px;align-items:flex-start}
.fcol li::before{content:"";width:0;height:0;border-left:6px solid var(--white);border-top:4px solid transparent;border-bottom:4px solid transparent;margin-top:9px}
.contact li::before{display:none}
.contact li{gap:12px}
.contact svg{flex:none;margin-top:6px}
.email-box{width:257px;height:38px;background:var(--white);font-size:11px;color:#888;padding:11px 14px}
.subscribe{margin-top:20px;width:134px;height:38px;line-height:38px;background:var(--blue);color:var(--white);text-align:center;font-size:12px;font-weight:600}
.copy{left:97px;top:3752px;font-size:11px;color:var(--white)}
.social-foot{left:990px;top:3740px;display:flex;gap:10px}
.social-foot span{width:30px;height:30px;border-radius:50%;background:var(--blue)}
.social-foot span:nth-child(2){background:#2a9fd8}
.social-foot span:nth-child(3){background:#b23a2c}
</style>
</head>
<body>

<header class="abs topbar"></header>
<div class="abs phone">
  <svg width="14" height="14" viewBox="0 0 24 24"><path fill="#1a5fb4" d="M6.6 10.8a15 15 0 006.6 6.6l2.2-2.2c.3-.3.7-.4 1-.2 1.1.4 2.3.6 3.6.6.6 0 1 .4 1 1V20c0 .6-.4 1-1 1A17 17 0 013 4c0-.6.4-1 1-1h3.5c.6 0 1 .4 1 1 0 1.3.2 2.5.6 3.6.1.3 0 .7-.2 1z"/></svg>
  Call us: (555) 014-2290
</div>
<div class="abs brand"><span class="dot"></span>Sunvale Bridal Atelier</div>
<div class="abs social-top"><span></span><span></span><span></span><span></span><span></span></div>

<nav class="abs nav">
  <span class="active">Home</span><span>About us</span><span>Team</span><span>Product</span><span>Blog</span><span>Contact Us</span>
</nav>

<section class="abs hero" role="img" aria-label="Black and white photograph of an embracing couple"></section>
<svg class="abs" style="left:0;top:700px" width="1200" height="140" viewBox="0 0 1200 140">
  <path d="M0 34 L120 48 L240 34 L380 60 L520 84 L600 130 L720 84 L860 60 L980 40 L1200 40 L1200 140 L0 140 Z" fill="#fff"/>
  <polyline points="0,34 120,48 240,34 380,60 520,84 600,130 720,84 860,60 980,40 1200,40" fill="none" stroke="#1a5fb4" stroke-width="6"/>
</svg>
<div class="abs hero-title">WAYFARER ESCAPES GLOBAL</div>
<div class="abs hero-sub">we will be offering the couples a travel<br>agency &amp; wedding consultant</div>
<div class="abs btn hero-btn">Read More</div>
<div class="abs dots hero-dots"><i class="on"></i><i></i><i></i><i></i></div>

<div class="abs about-photo" role="img" aria-label="Black and white portrait of a bride in a satin gown"></div>
<div class="abs about-frame"></div>
<article class="abs about-card">
  <h2>About us</h2>
  <p>Sed ut perspiciatis unde omnis iste natus error sit voluptatem accusantium doloremque laudantium, totam rem aperiam, eaque ipsa quae ab illo inventore veritatis et quasi architecto beatae vitae dicta sunt explicabo.Nemo enim ipsam voluptate quia voluptas sit aspernatur aut odit aut fugit, sed quia conseq magni dolores eos qui ratione voluptatem sequi nesciunt.</p>
  <span class="btn">Read More</span>
</article>

<section class="abs feature"></section>
<div class="abs feature-frame"></div>
<div class="abs feature-photo" role="img" aria-label="Photograph of a woman in a black dress and sunglasses on a city street"></div>
<div class="abs feature-text">
  <h2>Sunvale Bridal Atelier</h2>
  <p>Lorem ipsum dolor sit amet, consectetur adipiscing elit, sed do eiusmod tempor incididunt ut labore et dolore magna aliqua. Ut enim ad minim veniam, quis nostrud exercitation ullamco laboris nisi ut aliquip ex ea commodo consequat. Duis aute irure dolor in reprehenderit in voluptate velit esse cillum dolore eu fugiat nulla pariatur.</p>
  <span class="btn">Read More</span>
</div>

<section class="abs team" role="img" aria-label="Soft dark background photograph of a wedding scene"></section>
<svg class="abs" style="left:0;top:1895px" width="1200" height="80" viewBox="0 0 1200 80">
  <path d="M0 0 L1200 0 L1200 60 L1000 30 L860 50 L620 10 L480 40 L300 20 L0 60 Z" fill="#1556a8"/>
</svg>
<div class="abs team-title">Our Team</div>
<div class="abs member" style="left:172px">
  <div class="pic" role="img" aria-label="Portrait of a consultant in a dark suit"></div>
  <div class="info">
    <h3>Marcus<br>Hale</h3>
    <h4>Lorem Ipsum</h4>
    <p>Sed ut perspiciatis unde omnis iste natus error sit voluptatem accusantium</p>
    <div class="icons"><span></span><span></span><span></span></div>
  </div>
</div>
<div class="abs member" style="left:612px">
  <div class="info">
    <h3>Elena<br>Varga</h3>
    <h4>Lorem Ipsum</h4>
    <p>Sed ut perspiciatis unde omnis iste natus error sit voluptatem accusantium</p>
    <div class="icons"><span></span><span></span><span></span></div>
  </div>
  <div class="pic" role="img" aria-label="Portrait of a consultant in a dark blazer"></div>
</div>
<div class="abs dots team-dots"><i class="on"></i><i></i><i></i></div>

<div class="abs products-title">Our Products</div>
<div class="abs product" style="left:108px;top:2682px"><div class="pic" role="img" aria-label="Wedding gowns on display" style="background:linear-gradient(180deg,#d8d8d8,#f4f4f4)"></div><div class="label">Weddings Gowns</div></div>
<div class="abs product" style="left:445px;top:2682px"><div class="pic" role="img" aria-label="Row of black tuxedos" style="background:linear-gradient(180deg,#eee,#999)"></div><div class="label">Tuxedo</div></div>
<div class="abs product" style="left:782px;top:2682px"><div class="pic" role="img" aria-label="Lingerie corsets" style="background:linear-gradient(180deg,#fafafa,#6b5638)"></div><div class="label">Lingerie</div></div>
<div class="abs product" style="left:108px;top:2981px"><div class="pic" role="img" aria-label="Black leather dress shoes" style="background:linear-gradient(180deg,#fff,#bdbdbd)"></div><div class="label">Shoes</div></div>
<div class="abs product" style="left:445px;top:2981px"><div class="pic" role="img" aria-label="Flower girls in pink dresses with bouquets" style="background:linear-gradient(135deg,#e0306f,#f3a0b8 55%,#7fa25a)"></div><div class="label">Flower Girls Dress</div></div>
<div class="abs product" style="left:782px;top:2981px"><div class="pic" role="img" aria-label="Bridal boutique with gowns on racks" style="background:linear-gradient(135deg,#3a3a3a,#c9c3bd)"></div><div class="label">Wedding Gows</div></div>
<div class="abs dots prod-dots"><i class="on"></i><i></i><i></i></div>

<svg class="abs" style="left:0;top:3345px" width="1200" height="100" viewBox="0 0 1200 100">
  <path d="M0 100 L0 80 L160 70 L320 50 L480 44 L600 10 L720 44 L880 50 L1040 70 L1200 80 L1200 100 Z" fill="#1c1c1c"/>
  <polyline points="0,80 160,70 320,50 480,44 600,10 720,44 880,50 1040,70 1200,80" fill="none" stroke="#1a5fb4" stroke-width="6"/>
</svg>
<footer class="abs footer"></footer>
<div class="abs fcol contact" style="left:100px">
  <h5>CONTACT US</h5>
  <ul>
    <li><svg width="11" height="11" viewBox="0 0 24 24"><path fill="#fff" d="M2 11 22 2 13 22 11 13z"/></svg><span>12 Harbor Lane, Elm Row<br>Fairhaven, City Location</span></li>
    <li><svg width="11" height="11" viewBox="0 0 24 24"><path fill="#fff" d="M6.6 10.8a15 15 0 006.6 6.6l2.2-2.2c.3-.3.7-.4 1-.2 1.1.4 2.3.6 3.6.6.6 0 1 .4 1 1V20c0 .6-.4 1-1 1A17 17 0 013 4c0-.6.4-1 1-1h3.5c.6 0 1 .4 1 1 0 1.3.2 2.5.6 3.6.1.3 0 .7-.2 1z"/></svg><span>555-014-2290</span></li>
    <li><svg width="12" height="10" viewBox="0 0 24 18"><rect width="24" height="18" fill="#fff"/><path d="M0 0 12 10 24 0" fill="none" stroke="#1c1c1c" stroke-width="2"/></svg><span>info@sunvalebridal.com</span></li>
  </ul>
</div>
<div class="abs fcol" style="left:357px">
  <h5>QUICK LINKS</h5>
  <ul><li>Home</li><li>About</li><li>Team</li><li>Product</li><li>Blog</li><li>Contact Us</li></ul>
</div>
<div class="abs fcol" style="left:588px">
  <h5>OTHER LINKS</h5>
  <ul><li>Company</li><li>Privacy Policy</li><li>Terms &amp; Conditions</li><li>Our Clients</li></ul>
</div>
<div class="abs fcol" style="left:840px">
  <h5>NEWSLETTER</h5>
  <div class="email-box">Email ID</div>
  <div class="subscribe">SUBSCRIBE</div>
</div>
<div class="abs copy">Copyrights © 2018. Allrights Reserved.</div>
<div class="abs social-foot"><span></span><span></span><span></span></div>

</body>
</html>
```